Workshop PPT Update for AI Transformation Sessions

Our strategic consulting firm runs strategy workshops using slides as workshop exercises. These slides are used to communicate to the participants in advance, run the workshops and produce the final deliverable.

It is time for a design "upgrade". We'd like them to be more engaging, hipper and more interesting. These slides are utilitarian, so clean and usable is good. I have attached the example of what we have today. I have also attached an example of another company's slides that I like.

We can't rip off their design nor can we go away 100% from what we have. But I think it is possible to "update" our look to something closer to their look. Grey colors are fine with some color pop.

Slide styles needed are - 1) Cover Page, 2) Instructions Page, 3) Bullet list 4) Worksheet (place for participants to add content 5) Table, 6) Two column.

```html
<!DOCTYPE html>
<html lang="en">
<head>
<meta charset="utf-8">
<title>AI Transformation Workshop Slides</title>
<link href="https://fonts.googleapis.com/css2?family=Montserrat:wght@300;400;500;600;700&family=Archivo+Black&family=Arimo:wght@400;700&display=swap" rel="stylesheet">
<style>
  :root{
    --ink:#434654;
    --panel:#e9eaef;
    --panel-box:#575a6a;
    --red:#b23a36;
    --text:#3f4150;
    --rule:#a3a5ae;
    --cell-rule:#6f7180;
    --white:#ffffff;
  }
  *{box-sizing:border-box;margin:0;padding:0}
  html,body{width:1200px;height:3914px;overflow:hidden;background:var(--white)}
  body{position:relative;font-family:"Montserrat",Arial,sans-serif;color:var(--text)}
  .slide{position:absolute;left:88.5px;width:988.5px;height:555px;background:var(--panel);overflow:hidden}
  .side{position:absolute;left:0;top:0;width:325.5px;height:100%;background:var(--ink);color:var(--white)}
  .brand{position:absolute;font-family:"Montserrat",sans-serif;font-weight:500;font-size:15px;color:var(--ink);letter-spacing:-.2px}
  .num{position:absolute;width:42px;height:42px;border-radius:50%;background:var(--red);color:var(--white);
       font-weight:500;font-size:19px;display:flex;align-items:center;justify-content:center;transform:translate(-50%,-50%)}
  .num.sm{width:36px;height:36px;font-size:16px}

  /* Instructions slide */
  .slide--instructions{top:93px}
  .slide--instructions .side h1{position:absolute;left:0;width:300px;top:200px;text-align:center;font-weight:400;font-size:40px;line-height:60px;letter-spacing:1.5px}
  .step{position:absolute;left:460px;font-size:21px;font-weight:400;transform:translateY(-50%);white-space:nowrap}
  .step-rule{position:absolute;left:364.5px;width:577.5px;height:1.5px;background:var(--rule)}

  /* Cover slide */
  .slide--cover{top:705px}
  .cover-photo{position:absolute;inset:0;background:radial-gradient(ellipse at 72% 38%,#737889 0%,#50546a 45%,#3b3e4e 100%)}
  .cover-brand{position:absolute;width:100%;top:165px;text-align:center;color:var(--white);font-weight:400;font-size:45px}
  .cover-title{position:absolute;width:100%;top:255px;text-align:center;font-family:"Archivo Black",sans-serif;font-weight:400;font-size:42px;color:var(--white);letter-spacing:2px}
  .cover-subtitle{position:absolute;width:100%;top:328px;text-align:center;font-size:25px;font-weight:400;color:var(--white);letter-spacing:1px}

  /* Bullet list / overview slide */
  .slide--overview{top:1317px}
  .slide--overview .side h2{position:absolute;left:42px;top:52px;font-weight:700;font-size:32px;line-height:39px;letter-spacing:1px}
  .meta{position:absolute;left:44px;font-family:"Arimo",Arial,sans-serif;font-size:18px;transform:translateY(-50%)}
  .prep{position:absolute;left:45px;top:255px;width:226px;height:220px;background:var(--panel-box)}
  .prep h3{position:absolute;left:29px;top:24px;font-family:"Arimo",Arial,sans-serif;font-weight:400;font-size:18px}
  .prep li{position:absolute;left:46px;list-style:none;font-family:"Arimo",Arial,sans-serif;font-size:12px;transform:translateY(-50%);white-space:nowrap}
  .prep li::before{content:"";position:absolute;left:-17px;top:4px;width:7px;height:7px;border-radius:50%;background:var(--white)}
  .flow-title{position:absolute;left:369px;top:21px;font-size:24px;font-weight:500}
  .flow-item{position:absolute;left:420px;transform:translateY(-50%);white-space:nowrap}
  .flow-item b{display:block;font-weight:500;font-size:19px}
  .flow-item span{display:block;font-size:11px;margin-top:1px;padding-left:3px}
  .flow-divider{position:absolute;left:325.5px;right:0;top:442px;height:2px;background:var(--ink)}
  .deliverables{position:absolute;left:376px;top:467px;font-family:"Arimo",Arial,sans-serif;font-size:15px;font-weight:700}
  .deliverables span{display:block;font-weight:400;font-size:12px;margin-top:4px}

  /* Table slide */
  .slide--table{top:1929px}
  .title-accent{position:absolute;left:25.5px;top:0;width:174px;height:7px;background:var(--red)}
  .slide--table h2{position:absolute;left:31.5px;top:26px;font-size:24px;font-weight:600}
  .plan-table{position:absolute;left:27px;top:84px;width:928.5px;border-collapse:collapse;background:var(--white);
              box-shadow:0 6px 14px rgba(0,0,0,.12);table-layout:fixed;font-family:"Arimo",Arial,sans-serif;font-size:11px;font-weight:700;text-transform:uppercase;letter-spacing:.6px}
  .plan-table th{background:var(--ink);color:var(--white);height:43.5px;font-weight:700;text-align:left;padding-left:16px}
  .plan-table th.c{text-align:center;padding:0}
  .plan-table td{border:1.5px solid var(--cell-rule);vertical-align:top;padding:22px 0 0 16px;line-height:20px}
  .plan-table tr>td:first-child{border-left:none}
  .plan-table tr>td:last-child{border-right:none}
  .plan-table td.c{text-align:center;padding-left:0}
  .plan-table td.mid{vertical-align:middle;padding-top:0}
  .plan-table td.element{padding-left:37px}
  .plan-table .note{text-transform:none;font-weight:400;letter-spacing:0}

  /* Two-column slide */
  .slide--two-column{top:2541px}
  .slide--two-column h2{position:absolute;left:27px;top:19px;font-size:23px;font-weight:700;letter-spacing:1px;color:var(--ink)}
  .slide--two-column .side{top:66px;height:489px}
  .slide--two-column .side h3{position:absolute;left:30px;font-size:17px;font-weight:700;transform:translateY(-50%);white-space:nowrap}
  .slide--two-column .side li{position:absolute;left:52px;list-style:none;font-family:"Arimo",Arial,sans-serif;font-size:14px;transform:translateY(-50%);white-space:nowrap}
  .slide--two-column .side li::before{content:"";position:absolute;left:-20px;top:5px;width:8px;height:8px;border-radius:50%;background:var(--white)}
  .purpose{position:absolute;left:372px;top:80px;font-size:24px;font-weight:600;letter-spacing:1px;color:var(--ink)}
  .purpose-text{position:absolute;left:374px;top:118px;font-size:13.5px;font-weight:500}
  .badge{position:absolute;left:375px;top:163.5px;width:163.5px;height:33px;background:var(--red);color:var(--white);font-size:23px;font-weight:500;display:flex;align-items:center;justify-content:center}
  .instr{position:absolute;left:423px;transform:translateY(-50%);white-space:nowrap}
  .instr b{display:block;font-size:18px;font-weight:500}
  .instr span{display:block;font-size:11px;margin-top:1px}

  /* Worksheet slide */
  .slide--worksheet{top:3153px}
  .slide--worksheet .side h1{position:absolute;left:40.5px;top:171px;font-weight:400;font-size:40px;line-height:60px;letter-spacing:1.5px}
  .slide--worksheet .side p{position:absolute;left:41px;top:306px;font-family:"Arimo",Arial,sans-serif;font-size:15px;line-height:21px}
  .entry{position:absolute;left:355.5px;width:606px;height:84px;background:var(--white)}
  .entry svg{position:absolute;left:22.5px;top:21px}
  .entry h3{position:absolute;left:88.5px;top:13px;font-family:"Arimo",Arial,sans-serif;font-size:18px;font-weight:700}
  .entry p{position:absolute;left:88.5px;top:40px;width:505px;font-family:"Arimo",Arial,sans-serif;font-size:11.5px;line-height:16px}
</style>
</head>
<body>

<section class="slide slide--instructions">
  <div class="side"><h1>GETTING<br>STARTED</h1></div>
  <div class="num" style="left:412px;top:138px">1</div>
  <div class="step" style="top:138px">Complete the Engagement Sizing Survey</div>
  <div class="step-rule" style="top:177px"></div>
  <div class="num" style="left:412px;top:216px">2</div>
  <div class="step" style="top:216px">Collect relevant inputs.</div>
  <div class="step-rule" style="top:259.5px"></div>
  <div class="num" style="left:412px;top:294px">3</div>
  <div class="step" style="top:294px">Determine workshop participants &amp; date.</div>
  <div class="step-rule" style="top:333px"></div>
  <div class="num" style="left:412px;top:370px">4</div>
  <div class="step" style="top:370px">Send invites, to include pre-work.</div>
  <div class="brand" style="right:18px;top:512px">NorthPath</div>
</section>

<section class="slide slide--cover">
  <div class="cover-photo" role="img" aria-label="Business team reviewing charts and reports on a desk"></div>
  <div class="cover-brand">NorthPath</div>
  <h1 class="cover-title">KICKOFF &amp; DISCOVERY</h1>
  <div class="cover-subtitle">SIZING &amp; SCOPING AI TRANSFORMATION</div>
</section>

<section class="slide slide--overview">
  <div class="side">
    <h2>WORKSHOP<br>OVERVIEW</h2>
    <div class="meta" style="top:168px">Participants: Execs</div>
    <div class="meta" style="top:207px">Duration:&nbsp; 2 hrs.</div>
    <div class="prep">
      <h3>Prep Work:</h3>
      <ul>
        <li style="top:82px">Org Strategy</li>
        <li style="top:116px">2023 Goal Performance</li>
        <li style="top:150px">Existing policies</li>
        <li style="top:184px">Pre-thinking questions</li>
      </ul>
    </div>
  </div>
  <div class="flow-title">Workshop Flow</div>
  <div class="num sm" style="left:387px;top:93px">1</div>
  <div class="flow-item" style="top:93px"><b>Confirm Company Direction</b><span>Recap organizational purpose, values, vision &amp; winning strategy.</span></div>
  <div class="num sm" style="left:387px;top:150px">2</div>
  <div class="flow-item" style="top:150px"><b>Develop AI Vision</b></div>
  <div class="num sm" style="left:387px;top:207px">3</div>
  <div class="flow-item" style="top:202px"><b>Develop AI Guiding Principles</b><span>Developed AI Guiding Principles, supporting policies to include approved tools.</span></div>
  <div class="num sm" style="left:387px;top:270px">4</div>
  <div class="flow-item" style="top:265px"><b>Agree on a Governance Approach</b><span>Agreed upon governance approach, structure, &amp; executive champion.</span></div>
  <div class="num sm" style="left:387px;top:333px">5</div>
  <div class="flow-item" style="top:328px"><b>Agree on a Training &amp; Learning Approach</b><span>Set approach to training &amp; continuous learning.</span></div>
  <div class="num sm" style="left:387px;top:395px">6</div>
  <div class="flow-item" style="top:390px"><b>Determine Rollout &amp; Communication</b><span>Organizational rollout &amp; continuous communication</span></div>
  <div class="flow-divider"></div>
  <div class="deliverables">Deliverables<span>Your Company’s AI Playbook</span></div>
  <div class="brand" style="right:12px;top:523px">NorthPath</div>
</section>

<section class="slide slide--table">
  <div class="title-accent"></div>
  <h2>Plan Structure</h2>
  <table class="plan-table">
    <colgroup><col style="width:70.5px"><col style="width:121.5px"><col style="width:276px"><col style="width:219px"><col style="width:241.5px"></colgroup>
    <tr><th colspan="2" class="c">LEVEL</th><th>PLANNING ELEMENT &amp; DEFINITION</th><th>ACCOUNTABILITY/OWNER</th><th>FREQUENCY OF MODIFICATION</th></tr>
    <tr style="height:82.5px"><td>1</td><td>WHAT<br>(OVERALL)</td><td class="element">STRATEGIC PRIORITIES</td><td class="c">N/A</td><td class="c">3+ YEARS</td></tr>
    <tr style="height:84px"><td>1.1</td><td>WHAT<br>(THIS YEAR)</td><td class="element">GOALS<br><span class="note">Outcomes &amp; Strategies</span></td><td>EXECUTIVE LEADERSHIP</td><td class="c">1-3 YEARS</td></tr>
    <tr style="height:82.5px"><td>1.1.1</td><td rowspan="2" class="c mid">HOW</td><td class="element">KEY PERFORMANCE<br>INDICATORS AND/OR INITIATIVES</td><td></td><td class="c">1 YEAR<br>(W/ QRTLY TARGETS)</td></tr>
    <tr style="height:94.5px"><td>1.1.1.1</td><td class="element" style="padding-top:36px">ACTION ITEMS</td><td></td><td class="c" style="padding-top:36px">QUARTERLY/MONTHLY</td></tr>
  </table>
  <div class="brand" style="right:12px;top:519px">NorthPath</div>
</section>

<section class="slide slide--two-column">
  <h2>CREATING YOUR AI GUIDING PRINCIPLES</h2>
  <div class="side">
    <h3 style="top:54px">Your Existing Material</h3>
    <ul>
      <li style="top:91.5px">Company Values</li>
      <li style="top:120px">Current Policies (GDPR, CCPA, etc.)</li>
      <li style="top:148.5px">Legal Guidance</li>
      <li style="top:177px">OTHER</li>
    </ul>
    <h3 style="top:238.5px">Examples for Inspiration</h3>
    <ul><li style="top:277.5px">See next slides</li></ul>
    <h3 style="top:334.5px">PromptPal Prompts</h3>
    <ul><li style="top:373.5px">HERE</li></ul>
  </div>
  <div class="purpose">PURPOSE</div>
  <div class="purpose-text">To create behavioral statements that everyone is expected to adhere to.</div>
  <div class="badge">Instructions</div>
  <div class="num sm" style="left:390px;top:249px">1</div>
  <div class="instr" style="top:244px"><b>Create the Outline</b><span>Determine the topics that need a principle.</span></div>
  <div class="num sm" style="left:390px;top:306px">2</div>
  <div class="instr" style="top:301px"><b>Audit the Outline</b><span>Look at the current policies to determine if all topics are covered.</span></div>
  <div class="num sm" style="left:390px;top:360px">3</div>
  <div class="instr" style="top:360px"><b>Draft the Guiding Principles.</b></div>
  <div class="num sm" style="left:390px;top:409.5px">4</div>
  <div class="instr" style="top:409.5px"><b>Determine which GPs need detailed policies.</b></div>
  <div class="num sm" style="left:390px;top:457.5px">5</div>
  <div class="instr" style="top:457.5px"><b>Determine which AI Tools support the GPs.</b></div>
  <div class="num sm" style="left:390px;top:504px">6</div>
  <div class="instr" style="top:504px"><b>Finalize via a legal and executive review.</b></div>
  <div class="brand" style="right:12px;top:522px">NorthPath</div>
</section>

<section class="slide slide--worksheet">
  <div class="side">
    <h1>AI GUIDING<br>PRINCIPLES</h1>
    <p>What guides our decision-making<br>and approach?</p>
  </div>
  <div class="entry" style="top:19.5px">
    <svg width="42" height="42" viewBox="0 0 42 42" aria-hidden="true"><circle cx="21" cy="21" r="21" fill="#b23a36"/><circle cx="21" cy="21" r="9" fill="none" stroke="#fff" stroke-width="1.6"/><path d="M17 21l3 3 6-6" fill="none" stroke="#fff" stroke-width="1.6"/></svg>
    <h3>Principle #1</h3>
    <p>Complete perspective from Executives, Directors, Managers &amp; Staff. Conduct competitive analysis and customer research (optional).</p>
  </div>
  <div class="entry" style="top:115.5px">
    <svg width="42" height="42" viewBox="0 0 42 42" aria-hidden="true"><circle cx="21" cy="21" r="21" fill="#b23a36"/><circle cx="21" cy="21" r="9" fill="none" stroke="#fff" stroke-width="1.6"/><path d="M17 21l3 3 6-6" fill="none" stroke="#fff" stroke-width="1.6"/></svg>
    <h3>Principle #2</h3>
    <p>Complete perspective from Executives, Directors, Managers &amp; Staff. Conduct competitive analysis and customer research (optional).</p>
  </div>
  <div class="entry" style="top:213px">
    <svg width="42" height="42" viewBox="0 0 42 42" aria-hidden="true"><circle cx="21" cy="21" r="21" fill="#b23a36"/><circle cx="21" cy="21" r="9" fill="none" stroke="#fff" stroke-width="1.6"/><path d="M17 21l3 3 6-6" fill="none" stroke="#fff" stroke-width="1.6"/></svg>
    <h3>Principle #3</h3>
    <p>Complete perspective from Executives, Directors, Managers &amp; Staff. Conduct competitive analysis and customer research (optional).</p>
  </div>
  <div class="entry" style="top:309px">
    <svg width="42" height="42" viewBox="0 0 42 42" aria-hidden="true"><circle cx="21" cy="21" r="21" fill="#b23a36"/><circle cx="21" cy="21" r="9" fill="none" stroke="#fff" stroke-width="1.6"/><path d="M17 21l3 3 6-6" fill="none" stroke="#fff" stroke-width="1.6"/></svg>
    <h3>Principle #4</h3>
    <p>Complete perspective from Executives, Directors, Managers &amp; Staff. Conduct competitive analysis and customer research (optional).</p>
  </div>
  <div class="entry" style="top:406.5px">
    <svg width="42" height="42" viewBox="0 0 42 42" aria-hidden="true"><circle cx="21" cy="21" r="21" fill="#b23a36"/><circle cx="21" cy="21" r="9" fill="none" stroke="#fff" stroke-width="1.6"/><path d="M17 21l3 3 6-6" fill="none" stroke="#fff" stroke-width="1.6"/></svg>
    <h3>Principle #5</h3>
    <p>Complete perspective from Executives, Directors, Managers &amp; Staff. Conduct competitive analysis and customer research (optional).</p>
  </div>
  <div class="brand" style="right:22px;top:514px">NorthPath</div>
</section>

</body>
</html>
```